Sleek wordpress site for Bramblecrest finishing works

We are a commercial job shop that serves B2B, govt & LEO and retail clients.We need a wordpress site with 6 individual pages: homepage, coating, laser engraving, laser cutting, part marking, and contact us. I have attached an outline of the desired flow and sub headings for each page. I would like to incorporate the colors of the logo through out the site to be clean and sleek enough to appeal to B2B commercial clients yet be inviting enough for retail clients.

I would like to have easy picture functionality so photographs on each page can be updated easily.

Target Market(s)

B2B industrial & Govt and Military part marking, laser engraving and coating: machine shops, aerospace companies, tool manufactures. Retail: personalized gifts, Job Shop

Coding

Coded - Design and coding required

Font styles to use
Sans Serif
Other font styles liked:
• Open to suggestion

Colors
0255a3
3176b5
eaf1f7
cfdeed
ffffff

Requirements
Must have
• Clean easy to navigate flow, separate pages as indicated on attached outline, high class feel. Great picture functionality, professional and inviting feel,
• **update: needs to be optimized for mobile, should have a gallery function. Gallery can be an additional page or embedded
Nice to have
• Social media connectivity links,
Should not have
• crappy plugins that make back-end management difficult, no blog

```html
<!DOCTYPE html>
<html lang="en">
<head>
<meta charset="utf-8">
<title>Bramblecrest Finishing Works</title>
<link href="https://fonts.googleapis.com/css2?family=Open+Sans:wght@400;600&family=Roboto+Condensed:wght@400;700&display=swap" rel="stylesheet">
<style>
:root{
  --brand:#0255a3;
  --brand-mid:#3176b5;
  --brand-pale:#eaf1f7;
  --brand-soft:#cfdeed;
  --white:#ffffff;
  --ink:#1d1d1d;
  --body:#333333;
  --night:#0b0c0f;
  --heading-blue:#174a94;
}
*{box-sizing:border-box;margin:0;padding:0}
html,body{width:1200px;height:3010px;overflow:hidden}
body{position:relative;font-family:"Open Sans",Arial,sans-serif;color:var(--body);background:var(--white)}
.stage{position:absolute;left:0;top:0;width:1200px;height:3010px}
.abs{position:absolute}

/* header */
.topbar-item{display:flex;align-items:center;gap:14px;font-size:17px;color:#444}
.icon-ring{width:34px;height:34px;border:2px solid var(--brand-mid);border-radius:50%;display:flex;align-items:center;justify-content:center}
.brand-name{left:450px;top:38px;width:300px;text-align:center;font-family:"Roboto Condensed",sans-serif;font-weight:700;font-size:30px;line-height:34px;color:var(--brand);letter-spacing:.5px}

/* nav */
.main-nav{left:88px;top:160px;width:1022px;height:60px;background:linear-gradient(180deg,var(--brand-mid),var(--brand));box-shadow:0 3px 6px rgba(0,0,0,.35)}
.nav-home{position:absolute;left:0;top:0;width:108px;height:60px;background:#16181c;clip-path:polygon(0 0,100% 0,88% 100%,0 100%)}
.nav-search{position:absolute;right:0;top:0;width:82px;height:60px;background:#4a8ed0;clip-path:polygon(14% 0,100% 0,100% 100%,0 100%);display:flex;align-items:center;justify-content:center;padding-left:10px}
.nav-list{position:absolute;left:0;top:0;height:60px;display:flex;align-items:center;list-style:none;font-size:17px;color:var(--white);text-transform:uppercase}
.nav-list li{position:absolute;white-space:nowrap;top:19px}

/* hero */
.hero-caption{left:612px;top:432px;width:478px;height:196px;background:rgba(8,10,14,.88);clip-path:polygon(6% 0,100% 0,100% 100%,0 100%)}
.hero-frame{left:612px;top:452px;width:462px;height:172px;border:2px solid rgba(255,255,255,.85);border-left:none}
.hero-title{left:612px;top:470px;width:470px;text-align:center;font-family:"Roboto Condensed",sans-serif;color:var(--white)}
.hero-title .line1{font-size:52px;line-height:62px;display:block}
.hero-title .line2{font-size:38px;line-height:48px;display:block}
.slider-dot{width:22px;height:22px;border-radius:50%;background:rgba(40,40,40,.75);display:flex;align-items:center;justify-content:center}

/* sections */
.section-title{font-family:"Roboto Condensed",sans-serif;font-size:42px;font-weight:400}
.welcome-title{left:0;top:920px;width:1200px;text-align:center;color:var(--heading-blue)}
.welcome-copy{left:160px;top:996px;width:880px;text-align:center;font-family:Arial,sans-serif;font-size:15px;line-height:30px;color:#3a3a3a}
.btn-outline{height:38px;border:2px solid var(--brand-mid);background:rgba(255,255,255,.55);color:var(--heading-blue);font-size:15px;display:flex;align-items:center;justify-content:center}
.services-title{left:0;top:1396px;width:1200px;text-align:center;color:var(--white)}
.service-label{top:1740px;width:220px;text-align:center;font-family:"Roboto Condensed",sans-serif;font-size:23px;color:var(--white)}
.about-frame{left:120px;top:2036px;width:386px;height:274px;border:3px solid var(--brand)}
.about-title{left:573px;top:2056px;color:var(--heading-blue)}
.about-copy{left:573px;top:2118px;width:495px;font-family:Arial,sans-serif;font-size:14px;line-height:25.5px;color:#2a2a2a;text-align:justify}

/* footer */
.footer-head{top:2616px;font-size:21px;color:var(--white);text-transform:uppercase}
.contact-row{display:flex;gap:10px;color:var(--white)}
.contact-row strong{display:block;font-size:16px;font-weight:600;text-transform:uppercase}
.contact-row span{font-size:14px}
.footer-links{list-style:none;font-size:16px;color:var(--white);line-height:33px;top:2660px}
.form-field{left:800px;width:315px;height:36px;background:var(--white);border:1px solid #bbb;font-size:16px;color:#555;padding:6px 16px}
.send-btn{left:800px;top:2806px;width:128px;height:40px;background:var(--brand-mid);color:var(--white);font-size:19px;display:flex;align-items:center;justify-content:center}
.footer-rule{left:115px;top:2914px;width:1020px;height:1px;background:#4a4a4a}
.copyright{left:0;top:2945px;width:1200px;text-align:center;font-size:14px;color:#bdbdbd}
</style>
</head>
<body>
<div class="stage">
<svg class="abs" style="left:0;top:0" width="1200" height="3010" viewBox="0 0 1200 3010">
  <defs>
    <linearGradient id="lightBg" x1="0" y1="0" x2="1" y2="1">
      <stop offset="0" stop-color="#eef0f3"/><stop offset=".5" stop-color="#dfe3e8"/><stop offset="1" stop-color="#cfd4db"/>
    </linearGradient>
    <linearGradient id="heroPhoto" x1="0" y1="0" x2="1" y2="1">
      <stop offset="0" stop-color="#3d4a55"/><stop offset=".35" stop-color="#8fa1ad"/><stop offset=".6" stop-color="#5c6b76"/><stop offset="1" stop-color="#2c3238"/>
    </linearGradient>
    <radialGradient id="heroSpark" cx=".47" cy=".82" r=".25">
      <stop offset="0" stop-color="#e9734d" stop-opacity=".8"/><stop offset="1" stop-color="#e9734d" stop-opacity="0"/>
    </radialGradient>
    <linearGradient id="darkBg" x1="0" y1="0" x2="0" y2="1">
      <stop offset="0" stop-color="#0d0f13"/><stop offset=".5" stop-color="#2a2c30"/><stop offset="1" stop-color="#0a0b0d"/>
    </linearGradient>
    <linearGradient id="footBg" x1="0" y1="0" x2="0" y2="1">
      <stop offset="0" stop-color="#1a1b1e"/><stop offset="1" stop-color="#050505"/>
    </linearGradient>
    <linearGradient id="bandBlue" x1="0" y1="0" x2="1" y2="0">
      <stop offset="0" stop-color="#5f97d4"/><stop offset=".5" stop-color="#0d4aa0"/><stop offset="1" stop-color="#5f97d4"/>
    </linearGradient>
    <linearGradient id="hexA" x1="0" y1="0" x2="1" y2="1"><stop offset="0" stop-color="#e6e6ea"/><stop offset=".6" stop-color="#c7365a"/><stop offset="1" stop-color="#3a2430"/></linearGradient>
    <linearGradient id="hexB" x1="0" y1="0" x2="1" y2="1"><stop offset="0" stop-color="#f2f2f2"/><stop offset=".5" stop-color="#9ea4aa"/><stop offset="1" stop-color="#2b2e31"/></linearGradient>
    <linearGradient id="hexC" x1="0" y1="0" x2="1" y2="1"><stop offset="0" stop-color="#6c6a62"/><stop offset=".5" stop-color="#c9c5ba"/><stop offset="1" stop-color="#494844"/></linearGradient>
    <linearGradient id="hexD" x1="0" y1="0" x2="1" y2="1"><stop offset="0" stop-color="#c6c9cc"/><stop offset=".5" stop-color="#8d9196"/><stop offset="1" stop-color="#4d5156"/></linearGradient>
    <linearGradient id="videoPhoto" x1="0" y1="0" x2="1" y2="1"><stop offset="0" stop-color="#3a2a28"/><stop offset=".45" stop-color="#b75a36"/><stop offset=".7" stop-color="#f0b072"/><stop offset="1" stop-color="#4a2f26"/></linearGradient>
  </defs>

  <rect role="img" aria-label="Faded workshop backdrop with sparks" width="1200" height="3010" fill="url(#lightBg)"/>

  <!-- hero -->
  <g role="img" aria-label="Laser cutting head sending sparks across a metal sheet">
    <polygon points="0,190 1200,190 1200,712 600,815 0,712" fill="url(#heroPhoto)"/>
    <polygon points="0,190 1200,190 1200,712 600,815 0,712" fill="url(#heroSpark)"/>
  </g>
  <polygon points="0,710 600,813 1200,710 1200,730 600,846 0,730" fill="url(#bandBlue)"/>

  <!-- services -->
  <polygon points="0,1222 600,1318 1200,1222 1200,1800 600,1888 0,1800" fill="url(#darkBg)" role="img" aria-label="Dark workshop backdrop"/>
  <polygon points="0,1212 600,1298 1200,1212 1200,1228 600,1326 0,1228" fill="url(#bandBlue)"/>
  <polygon points="0,1796 600,1884 1200,1796 1200,1816 600,1936 0,1816" fill="url(#bandBlue)"/>
  <polygon points="0,1796 600,1884 1200,1796 1200,1800 600,1890 0,1800" fill="#0e1014"/>

  <g stroke="#5f95ad" stroke-width="2">
    <polygon role="img" aria-label="Laser engraving beam on metal" points="260,1480 362,1538 362,1656 260,1714 158,1656 158,1538" fill="url(#hexA)"/>
    <polygon role="img" aria-label="Laser cutting nozzle over a plate" points="486,1480 588,1538 588,1656 486,1714 384,1656 384,1538" fill="url(#hexB)"/>
    <polygon role="img" aria-label="Part marking machine on a steel part" points="712,1480 814,1538 814,1656 712,1714 610,1656 610,1538" fill="url(#hexC)"/>
    <polygon role="img" aria-label="Coated parts on a rack" points="938,1480 1040,1538 1040,1656 938,1714 836,1656 836,1538" fill="url(#hexD)"/>
  </g>
  <path d="M104 1580 L90 1596 L104 1612" stroke="#fff" stroke-width="2.5" fill="none"/>
  <path d="M1094 1580 L1108 1596 L1094 1612" stroke="#fff" stroke-width="2.5" fill="none"/>

  <!-- about video -->
  <rect role="img" aria-label="Video still of a laser cutter throwing sparks" x="140" y="2056" width="386" height="276" fill="url(#videoPhoto)"/>
  <circle cx="333" cy="2186" r="30" fill="rgba(20,20,20,.45)" stroke="#fff" stroke-width="3"/>
  <polygon points="324,2170 346,2186 324,2202" fill="#fff"/>

  <!-- footer -->
  <polygon points="0,2395 600,2500 1200,2395 1200,3010 0,3010" fill="url(#footBg)" role="img" aria-label="Dark footer backdrop"/>
  <polygon points="0,2384 600,2478 1200,2384 1200,2402 600,2522 0,2402" fill="url(#bandBlue)"/>
</svg>

<!-- header -->
<div class="abs topbar-item" style="left:88px;top:56px">
  <span class="icon-ring"><svg width="16" height="16" viewBox="0 0 24 24"><path d="M6.6 10.8a15 15 0 006.6 6.6l2.2-2.2a1 1 0 011-.25 11 11 0 003.6.6 1 1 0 011 1V20a1 1 0 01-1 1A17 17 0 013 4a1 1 0 011-1h3.5a1 1 0 011 1 11 11 0 00.6 3.6 1 1 0 01-.25 1z" fill="none" stroke="#3176b5" stroke-width="2"/></svg></span>
  <span>555.214.0387</span>
</div>
<div class="abs brand-name">BRAMBLECREST<br>FINISHING WORKS</div>
<div class="abs topbar-item" style="left:888px;top:50px">
  <span class="icon-ring"><svg width="16" height="18" viewBox="0 0 24 26"><path d="M12 25s8-8.5 8-14a8 8 0 00-16 0c0 5.5 8 14 8 14z" fill="none" stroke="#3176b5" stroke-width="2.4"/><circle cx="12" cy="11" r="3" fill="#3176b5"/></svg></span>
  <span style="line-height:24px">418 N Harlow Ave #210,<br>Fenwick, AZ 85990</span>
</div>

<nav class="abs main-nav">
  <div class="nav-home"></div>
  <ul class="nav-list">
    <li style="left:29px">Home</li>
    <li style="left:126px">Coating</li>
    <li style="left:248px">Laser Engraving</li>
    <li style="left:446px">Laser Cutting</li>
    <li style="left:620px">Part Marking</li>
    <li style="left:790px">Contact Us</li>
  </ul>
  <div class="nav-search"><svg width="22" height="22" viewBox="0 0 24 24"><circle cx="10" cy="10" r="6.5" fill="none" stroke="#fff" stroke-width="2.8"/><path d="M15 15l6 6" stroke="#fff" stroke-width="3"/></svg></div>
</nav>

<!-- hero -->
<div class="abs hero-caption"></div>
<div class="abs hero-frame"></div>
<div class="abs hero-title"><span class="line1">Bramblecrest Finishing</span><span class="line2">Cutting Service</span></div>
<div class="abs slider-dot" style="left:44px;top:530px"><svg width="10" height="10" viewBox="0 0 10 10"><path d="M7 1L3 5l4 4" stroke="#fff" stroke-width="1.8" fill="none"/></svg></div>
<div class="abs slider-dot" style="left:1156px;top:510px"><svg width="10" height="10" viewBox="0 0 10 10"><path d="M3 1l4 4-4 4" stroke="#fff" stroke-width="1.8" fill="none"/></svg></div>

<!-- welcome -->
<h1 class="abs section-title welcome-title">Welcome to Bramblecrest Finishing</h1>
<p class="abs welcome-copy">The point of using Lorem Ipsum is that it has a more-or-less normal distribution of letters, as opposed to using 'Content here, content here', making it look like readable English. Many desktop publishing packages and web page editors now use Lorem Ipsum as their default model text, and a search for 'lorem ipsum' will uncover many web sites still in their infancy. Various versions have evolved over the years, sometimes by accident, sometimes</p>
<a class="abs btn-outline" style="left:535px;top:1152px;width:130px">Read More »</a>

<!-- services -->
<h2 class="abs section-title services-title">Our Services</h2>
<div class="abs service-label" style="left:143px">Laser engraving</div>
<div class="abs service-label" style="left:365px">Laser Cutting</div>
<div class="abs service-label" style="left:596px">Part Marking</div>
<div class="abs service-label" style="left:829px">Coatings</div>

<!-- who we are -->
<div class="abs about-frame"></div>
<h2 class="abs section-title about-title">Who We Are</h2>
<p class="abs about-copy">It is a long established fact that a reader will be distracted by the readable content of a page when looking at its layout. The point of using Lorem Ipsum is that it has a more-or-less normal distribution of letters, as opposed to using 'Content here, content here', making it look like readable English. Many desktop publishing packages and web page editors now use Lorem Ipsum as their default model text, and a search for 'lorem ipsum' will uncover many</p>
<a class="abs btn-outline" style="left:571px;top:2292px;width:128px">Read More »</a>

<!-- footer -->
<div class="abs footer-head" style="left:100px">Contact Us</div>
<div class="abs contact-row" style="left:100px;top:2674px">
  <svg width="22" height="18" viewBox="0 0 24 18"><rect x="1" y="1" width="22" height="16" fill="none" stroke="#fff" stroke-width="1.6"/><path d="M1 1l11 9 11-9" fill="none" stroke="#fff" stroke-width="1.6"/></svg>
  <div><strong>Email Address</strong><span>info@bramblecrest.example</span></div>
</div>
<div class="abs contact-row" style="left:100px;top:2740px">
  <svg width="22" height="22" viewBox="0 0 24 24"><path d="M6.6 10.8a15 15 0 006.6 6.6l2.2-2.2a1 1 0 011-.25 11 11 0 003.6.6 1 1 0 011 1V20a1 1 0 01-1 1A17 17 0 013 4a1 1 0 011-1h3.5a1 1 0 011 1 11 11 0 00.6 3.6 1 1 0 01-.25 1z" fill="none" stroke="#fff" stroke-width="1.6"/></svg>
  <div><strong>Phone Number</strong><span>555.214.0387</span></div>
</div>

<div class="abs footer-head" style="left:395px">Links</div>
<ul class="abs footer-links" style="left:396px"><li>Home</li><li>About Us</li><li>Services</li><li>Coating</li></ul>

<div class="abs footer-head" style="left:572px">Resources</div>
<ul class="abs footer-links" style="left:573px"><li>Laser engraving</li><li>Laser cutting</li><li>Part marking</li><li>Contact us</li></ul>

<div class="abs footer-head" style="left:798px">Get in Touch</div>
<div class="abs form-field" style="top:2668px">Your Name</div>
<div class="abs form-field" style="top:2713px">Email address</div>
<div class="abs form-field" style="top:2758px">Phone</div>
<div class="abs send-btn">SEND</div>

<div class="abs footer-rule"></div>
<div class="abs copyright">© 2018 Company Name &nbsp;All right reserved</div>
</div>
</body>
</html>
```